Specialised investor in e-mobility and energy wants business card design

We need a business card design that fits our existing corporate design. <The look and feel must be 'sharp'/'clean', dynamic, communicate momentum, professionalism etc (as one would imagine from a firm in the financial sector). We like the idea of a reverse-side of the card that includes the logo, and the name and contact details on the other. We expect the deliverable to be whatever format might be required to be able to get cards printed directly by a service such as kelmo press. Our website is www.zub.capital

```html
<!DOCTYPE html>
<html lang="en">
<head>
<meta charset="utf-8">
<title>ZUB Capital – Business Card</title>
<link rel="stylesheet" href="https://fonts.googleapis.com/css2?family=Montserrat:wght@400;600;700;800&family=Quicksand:wght@400;500&display=swap">
<style>
  :root {
    --page-bg: #e6e2dc;
    --card-light: #eeebe6;
    --card-dark: #1c1c1b;
    --card-dark-edge: #3a3937;
    --green: #7ba83a;
    --green-deep: #2e5a1f;
    --text-light: #dcd8d0;
    --text-muted: #b9b3a8;
  }
  * { margin: 0; padding: 0; box-sizing: border-box; }
  html, body {
    width: 1200px; height: 1047px; overflow: hidden;
    background: var(--page-bg);
  }
  .card {
    position: absolute;
    left: 160px; top: 283px;
    width: 880px; height: 480px;
    border-radius: 22px;
    overflow: hidden;
    background: var(--card-light);
    box-shadow: 0 10px 30px rgba(0,0,0,0.18);
    font-family: "Montserrat", sans-serif;
  }
  .card-shapes { position: absolute; inset: 0; }
  .brand {
    position: absolute; left: 50px; top: 56px;
    display: flex; align-items: center; gap: 14px;
    font-family: "Quicksand", sans-serif;
    font-weight: 500; font-size: 44px;
    color: var(--text-light);
    letter-spacing: 0.5px;
  }
  .brand-dot {
    width: 18px; height: 18px; border-radius: 50%;
    background: var(--text-light);
  }
  .name-tab {
    position: absolute; left: 0; top: 176px;
    width: 22px; height: 36px;
    background: var(--green);
    border-radius: 0 8px 8px 0;
  }
  .holder-name {
    position: absolute; left: 46px; top: 168px;
    font-weight: 700; font-size: 30px; letter-spacing: 0.8px;
    color: var(--green);
  }
  .holder-role {
    position: absolute; left: 46px; top: 208px;
    font-size: 21px; color: var(--text-light);
  }
  .contacts {
    position: absolute; left: 46px; top: 264px;
    list-style: none;
    font-size: 22px; color: var(--text-light);
  }
  .contacts li {
    display: flex; align-items: center; gap: 10px;
    height: 32px;
  }
  .contacts svg { width: 18px; height: 18px; fill: var(--green); }
  .office {
    position: absolute; left: 42px; top: 384px;
    font-size: 22px; line-height: 32px;
  }
  .office-company { color: var(--green); }
  .office-city { color: var(--text-muted); }
  .reverse-name {
    position: absolute; left: 540px; top: 170px;
    font-weight: 800; font-size: 132px; letter-spacing: 2px;
    color: var(--green-deep);
    line-height: 1;
  }
</style>
</head>
<body>
  <article class="card">
    <svg class="card-shapes" viewBox="0 0 880 480" width="880" height="480" aria-hidden="true">
      <defs>
        <linearGradient id="dark-panel" x1="0" y1="0" x2="1" y2="0">
          <stop offset="0" stop-color="var(--card-dark)"/>
          <stop offset="0.75" stop-color="#262524"/>
          <stop offset="1" stop-color="var(--card-dark-edge)"/>
        </linearGradient>
      </defs>
      <path d="M0 0 H575 C470 120 420 300 480 480 H0 Z" fill="url(#dark-panel)"/>
      <path d="M585 0 H632 C500 120 440 320 512 480 H495 C420 320 470 110 585 0 Z" fill="var(--green)"/>
      <path d="M470 140 C420 240 410 380 470 480 H456 C400 380 410 240 470 140 Z" fill="var(--green-deep)"/>
    </svg>

    <div class="brand"><span class="brand-dot"></span>ZUB Capital</div>

    <span class="name-tab"></span>
    <h1 class="holder-name">MARK HOLLEN</h1>
    <p class="holder-role">Managing Director</p>

    <ul class="contacts">
      <li>
        <svg viewBox="0 0 24 24"><path d="M4 9c0-3 4-5 8-5s8 2 8 5l-3 1-1-2H8L7 10 4 9Zm3 3h10l2 8H5l2-8Zm5 2a2 2 0 1 0 0 4 2 2 0 0 0 0-4Z"/></svg>
        +41 70123 4567
      </li>
      <li>
        <svg viewBox="0 0 24 24"><path d="M3 6h18v12H3V6Zm2 2v.5l7 5 7-5V8l-7 5-7-5Z"/></svg>
        mark@zub.capital
      </li>
      <li>
        <svg viewBox="0 0 24 24"><circle cx="12" cy="12" r="9"/></svg>
        www.zub.capital
      </li>
    </ul>

    <div class="office">
      <p class="office-company">ZUB Capital S.A.</p>
      <p class="office-city">Brevaux, Vellonia</p>
    </div>

    <p class="reverse-name">ZUB</p>
  </article>
</body>
</html>
```